The Korvessel Bands: Vesperance Paranormal Romance Cover Contest

Adult paranormal romance cover & e-cover (jpeg longest side not to exceed 2500 pixels, 1600 x 2500 uploads fine), 72 dpi, RGB. Plus, paperback pdf with back approximately 254 pages, .64 spine (16.26 mm), 300dpi, bleed .5, size 5.5 x 8.5. leave room for ISBN on back bottom right. Books 1 and 2 of series (The Korvessel Bands: Lantern/ & Harborlight) are on Brindlecart.example. Author name L. M. Garrow, for reference. New font will need to be selected. For book 3 Vesperance, I am hoping for an inverted Egyptian pyramid, prefer nighttime because that is when they will break into the Giza in order to find Isis's hidden amber amulet. The title Vesperance happens because the main character can see the secret inverted doorway inside the Giza that accesses Isis's hidden room. The main character's (Mabel & Corvin) will have a tattoo magically created on them (heart area) during the immortal ceremony. The tattoo is planned as an inverted pyramid with the arabic symbol/word for Hidden on top of (or could use a simple triangle whatever works best). If a human element is needed Mabel has light brown hair, multi-tonal, and blue-green eyes, wears ponytails a lot almost age 17, her soon to be immortal mate Corvin De Lacey (actor Brent Lomaski was my inspiration for the look of the character include snapshot as reference only) is desperately trying to prevent Mabel from dying and becoming a portal (she gets engulfed in bright light floating off her bed in one scene another scene the light glows behind her eyes). The tattoo also has ribbons of amber weaved in it symbolic of the amulet they are searching for. Isis's amulet will let her control the portal so she can live. The overall series is about a team of 8 immortal guardians that are each fated for one person if their magical ring doesn't find them then they might turn into the evil they are protecting mankind from. The first half of the book is set in Salem, MA there is a scene with Spirovo board that tells them to find the amulet and go to Egypt or die (another idea for cover is the eye from the Spirovo board maybe over a map of Egypt.) Before breaking into the Giza they trek through the desert with a team to a Sunken Obelisk to get clues. The Sunken Obelisk is buried in sand and they magically move the sand to access it. I have uploaded a snapshot from pixel vault that reminds me of Mabel especially her eyes, but I have not purchased any of the snapshots. Also included Arabic word for hidden. Any photos used will have to have basic rights to the photo. My author pic is upload black and white with glasses and pdf of back summary. Hope I've included enough info. Thanks, L. M. Garrow
Open to artistic ideas.

ADDING INFORMATION 9/14: All of the above is correct. A few additional comments in general but are not in anyway needed to be added. Everyone's work is awesome! The series is based in 2023. All of the immortals (7 guys, 1 women are bad to the bone warriors - there is nothing soft about them and killing is what they do best but times have changed and they are more refined and blend into society.) Book 3 Vesperance is Corvin's story he is the super brains, super hot ladies' man of the group and he goes undercover at Salem, MA high school where at first he doesn't know it but he meets his mate Mabel - she's a nobody under baggy clothes. Corvin will need to help save Mabel or she dies. Their big mission is to go to Egypt to get Isis's amulet after they play jokingly Spirovo board with friends at Crowfeather Hollow that talks directly to Mabel. Mabel is changing into a portal. The amulet is the only way for her to not die and be able to control the portal. Part of her changing is that her vision is changing hence I called the book Vesperance because she is seeing things inverted or that others aren't able to see without the help of magical glasses. So they go to the Sunken Obelisk and use magic to gain entrance looking for clues which they get then they break into the Giza at night for the grand finale. The immortal ceremony happens inside the Giza where the leader strikes lightning into Mabel's heart and at that moment The Korvessel Band (looks ancient/viking like) (each immortal has) divides identically for the chosen mate and a tattoo is engraved over their heart. Each immortal has a different symbol one that represents the couple. Though I can modify how I wrote it based on designs, at present it is an inverted triangle or pyramid with amber ribbons and the arabic word/symbol for hidden. One other element that does come up in the novel is the magical tropical yellow flower from the deadly Karakoram Mountain, that they had to get first to help save her. It has healing powers. When the flower is still in bloom it is just waved/touched and it heals. As it dies super smart Corvin crushes it up and has Mabel drink the petals. Well I hope the extra comments helped. As soon as I figure out how to put designers in my like pile I will be excited to have you work on future projects. The series has 8 total planned with a spin off series for their kids. Also all the adult books are also being modified for young adult. That's a lot of covers. So thank you all for such great submissions. Sorry I haven't used the star rating yet but I'm not sure I like what the stars represent. As we come into the final days I will mark off the stars. Thanks again for all the hard work.

Target Market(s)

Primarily Women 18+

Industry/Entity Type

Adult

Font styles to use
Serif
Script

Requirements
Nice to have
• Open on font style. Open on colors though main characters eyes are emphasized in book blue-green and are referred to as color of an Ammolite gem. The only other main colors are the bright light of the portal and Isis's amber amulet.

```html
<!DOCTYPE html>
<html lang="en">
<head>
<meta charset="utf-8">
<title>The Korvessel Band – Vesperance – Back Cover</title>
<link rel="stylesheet" href="https://fonts.googleapis.com/css2?family=Cinzel+Decorative:wght@700;900&family=Pirata+One&family=Cinzel:wght@600&family=Crimson+Text:ital,wght@0,700;1,400&family=Great+Vibes&display=swap">
<style>
  :root {
    --bg-deep: #2a0508;
    --bg-mid: #6e1016;
    --bg-glow: #a3262a;
    --title-white: #f6f1ec;
    --title-edge: #7a0d12;
    --tagline-gold: #f3d25a;
    --body-white: #fbf7f2;
    --note-gold: #e9c46a;
    --rule: #d6a94a;
    --isbn-white: #ffffff;
  }
  html, body {
    margin: 0;
    padding: 0;
    overflow: hidden;
  }
  .back-cover {
    position: relative;
    width: 778px;
    height: 1200px;
    overflow: hidden;
    background:
      radial-gradient(ellipse 60% 40% at 80% 15%, rgba(255,170,120,0.18), transparent 70%),
      radial-gradient(ellipse 70% 55% at 25% 75%, rgba(190,40,40,0.35), transparent 70%),
      radial-gradient(ellipse 120% 90% at 50% 45%, var(--bg-glow) 0%, var(--bg-mid) 45%, var(--bg-deep) 100%);
    font-family: "Crimson Text", Georgia, serif;
    color: var(--body-white);
  }
  .series-title {
    position: absolute;
    top: 18px;
    left: 0;
    width: 100%;
    margin: 0;
    text-align: center;
    font-family: "Cinzel Decorative", serif;
    font-weight: 900;
    font-size: 48px;
    line-height: 1;
    color: var(--title-white);
    text-shadow: 0 0 2px var(--title-edge), 2px 2px 0 var(--title-edge), 0 0 12px rgba(0,0,0,0.6);
  }
  .title-link {
    position: absolute;
    top: 78px;
    left: 0;
    width: 100%;
    text-align: center;
    font-family: "Cinzel", serif;
    font-weight: 600;
    font-size: 13px;
    letter-spacing: 6px;
    color: var(--title-white);
    text-shadow: 1px 1px 0 var(--title-edge);
  }
  .book-title {
    position: absolute;
    top: 92px;
    left: 0;
    width: 100%;
    margin: 0;
    text-align: center;
    font-family: "Pirata One", serif;
    font-weight: 400;
    font-size: 52px;
    line-height: 1;
    color: var(--title-white);
    text-shadow: 2px 2px 0 var(--title-edge), 0 0 10px rgba(0,0,0,0.6);
  }
  .emblem {
    position: absolute;
    top: 148px;
    left: 368px;
    width: 42px;
    height: 32px;
  }
  .tagline {
    position: absolute;
    top: 186px;
    left: 40px;
    width: 698px;
    margin: 0;
    text-align: center;
    font-weight: 700;
    font-size: 21px;
    line-height: 1.3;
    color: var(--tagline-gold);
  }
  .excerpt {
    position: absolute;
    left: 32px;
    width: 714px;
    margin: 0;
    font-style: italic;
    font-size: 15.6px;
    line-height: 1.62;
    text-align: justify;
  }
  .excerpt-mabel { top: 252px; }
  .excerpt-corvin { top: 486px; }
  .edition-note {
    position: absolute;
    top: 748px;
    left: 32px;
    width: 714px;
    padding-top: 10px;
    border-top: 1px solid var(--rule);
    font-family: "Cinzel", serif;
    font-weight: 600;
    font-size: 10.5px;
    letter-spacing: 0.4px;
    color: var(--note-gold);
  }
  .author-photo {
    position: absolute;
    top: 790px;
    left: 31px;
    width: 208px;
    height: 236px;
  }
  .isbn-space {
    position: absolute;
    top: 790px;
    left: 467px;
    width: 213px;
    height: 228px;
    background: var(--isbn-white);
  }
  .author-name {
    position: absolute;
    top: 1030px;
    left: 26px;
    font-family: "Great Vibes", cursive;
    font-size: 48px;
    line-height: 1.2;
    color: var(--title-white);
    text-shadow: 1px 1px 3px rgba(0,0,0,0.6);
  }
</style>
</head>
<body>
<main class="back-cover">
  <h1 class="series-title">The Korvessel Band</h1>
  <div class="title-link">SURVIVES</div>
  <h2 class="book-title">Vesperance</h2>

  <svg class="emblem" viewBox="0 0 42 32" role="img" aria-label="Small dark emblem illustration">
    <defs>
      <radialGradient id="emblemTone" cx="50%" cy="50%" r="50%">
        <stop offset="0%" stop-color="#5a5a66"/>
        <stop offset="100%" stop-color="#1c1418"/>
      </radialGradient>
    </defs>
    <rect width="42" height="32" rx="5" fill="url(#emblemTone)"/>
  </svg>

  <p class="tagline">Time is running out to save Mabel, and Corvin will stop at nothing to make sure she survives the vesperance.</p>

  <p class="excerpt excerpt-mabel">~ Mabel ~ Geez, that stupid jock tripped me again. I patted the hallway floor of Salem High searching for my glasses. A pair of tennis shoes appeared in my blurred vision. I stole a secretive glance as he offered a very masculine hand to me. Taking hold, I avoided his eyes, because I just knew I'd look like Fernlet staring into oncoming traffic. He was that hot. I barely remembered to let go of his hand as I stumbled off in front of him. I think he asked me where his class was. I must have mumbled something, because he's following me, and now I barely remember where I'm going.</p>

  <p class="excerpt excerpt-corvin">~ Corvin ~ My protective instincts kicked into overdrive when I saw her fall. I hurried over scooping up her glasses while reaching for her hand. The gentle zap took me by surprise as her fingers wrapped over mine. Static electricity — my logic countered, but my stomach clenched in disagreement. I followed her swinging ponytail knowing I just found a friend, and it would appear she was sorely in need of one. Hopefully, she can shed some light on the odd occurrences happening around town. That was why I was here, after all, to destroy any threat to humanity. Hopefully, I will have the problem fixed in no time at all. My stomach gave another tightening at my thought, and I wondered the cause as I studied the petite girl in front of me.</p>

  <div class="edition-note">THE FOLLOWING BOOK IS A REVISED YA EDITION OF THE ADULT TITLE, THE KORVESSEL BANDS: VESPERANCE</div>

  <svg class="author-photo" viewBox="0 0 208 236" role="img" aria-label="Black and white author portrait">
    <defs>
      <linearGradient id="photoTone" x1="0" y1="0" x2="0" y2="1">
        <stop offset="0%" stop-color="#b5b5b5"/>
        <stop offset="100%" stop-color="#4a4a4a"/>
      </linearGradient>
    </defs>
    <rect width="208" height="236" fill="url(#photoTone)"/>
  </svg>

  <div class="isbn-space" aria-label="Space reserved for ISBN"></div>

  <div class="author-name">L. M. Garrow</div>
</main>
</body>
</html>
```